High-end construction company needs a business card design

We need a modern looking business card that draws people in, is memorable and looks so good people will want to sick it on their fridges.
On the first side what is needed are:
Logo
My name - Tomasz Brelwik
Title - Managing Director
Website - www.varkelt.co.uk
Email - tomasz@varkelt.co.uk
Telephone - 020 5194 6281
Mobile - 07845139072
On the back side was is needed is a list of all the services we provide:
-Kitchen Renovations
-Bathroom Renovations
-House Renovations
-Garage Conversions
-Extensions
-Loft Conversions
-Conservatories
-Carpentry
-Tiling
-Electrical
-Plumbing & Heating
-Bricklaying
-Landscaping
-Decorating
-Plastering
We would like the colours to be the same shades as on the logo with grey or black for the words.
Target Market(s)
Anyone who needs building work done
Contact Information for Business Card
This business card is for a construction company which strives to deliver excellent service and quality.
The look and feel of the card should represent this.
Requirements
Must have
- On the first side what is needed are:
Logo
My name - Tomasz Brelwik
Title - Managing Director
Website - www.varkelt.co.uk
Email - tomasz@varkelt.co.uk
Telephone - 020 5194 6281
Mobile - 07845139072
Nice to have
- Cool looking features

```html
<!DOCTYPE html>
<html lang="en">
<head>
<meta charset="utf-8">
<title>Varkelt Construction Ltd – Business Card</title>
<link rel="stylesheet" href="https://fonts.googleapis.com/css2?family=Roboto:wght@400;700&display=swap">
<style>
  :root {
    --page-bg: #e9e7e6;
    --card-surface: #f5f3f3;
    --brand-green: #72bf44;
    --brand-green-deep: #4a8f40;
    --logo-green: #6cbc45;
    --logo-faint: #cfe3c3;
    --text-light: #ffffff;
    --divider: rgba(255,255,255,0.8);
  }
  * { box-sizing: border-box; margin: 0; padding: 0; }
  html, body {
    width: 1200px; height: 1181px; overflow: hidden;
    background: var(--page-bg);
    font-family: "Roboto", Arial, sans-serif;
  }
  .canvas { position: relative; width: 1200px; height: 1181px; }

  .card {
    position: absolute; width: 655px; height: 404px;
    background: var(--card-surface);
    box-shadow: 0 10px 30px rgba(0,0,0,0.12);
    overflow: hidden;
  }
  .card--front { left: 180px; top: 156px; }
  .card--back  { left: 480px; top: 627px; }

  .brand {
    position: absolute; left: 0; right: 0; top: 0; height: 226px;
    display: flex; flex-direction: column; align-items: center; justify-content: center;
    padding-top: 40px;
    font-weight: 700; color: var(--logo-green); text-transform: uppercase;
  }
  .brand__name { font-size: 64px; line-height: 1; letter-spacing: 1px; }
  .brand__line { font-size: 15px; letter-spacing: 4.2px; margin-top: 8px; }
  .brand--faint { color: var(--logo-faint); }

  .band {
    position: absolute; left: 0; right: 0; bottom: 0; height: 178px;
    color: var(--text-light);
  }
  .band--front { background: var(--brand-green); }
  .band--back  { background: var(--brand-green-deep); height: 175px; }

  .person {
    position: absolute; right: 355px; top: 55px; text-align: right;
  }
  .person__name { font-size: 25px; font-weight: 700; line-height: 1.1; letter-spacing: -0.2px; }
  .person__title { font-size: 19px; margin-top: 6px; }

  .divider {
    position: absolute; left: 322px; top: 34px; width: 1px; height: 92px;
    background: var(--divider);
  }

  .contacts { position: absolute; left: 346px; top: 33px; list-style: none; }
  .contacts li {
    display: flex; align-items: center; height: 23.7px; font-size: 19px;
  }
  .contacts svg { width: 17px; height: 17px; margin-right: 8px; flex: none; }

  .services {
    position: absolute; top: 22px; list-style: none; font-size: 19px;
  }
  .services li { height: 23.6px; line-height: 23.6px; display: flex; align-items: center; }
  .services li::before {
    content: ""; width: 8px; height: 8px; border-radius: 50%;
    background: var(--text-light); margin-right: 7px; flex: none;
  }
  .services--one   { left: 27px; }
  .services--two   { left: 256px; }
  .services--three { left: 436px; top: 20px; }
</style>
</head>
<body>
<div class="canvas">

  <section class="card card--front">
    <div class="brand">
      <span class="brand__name">Varkelt</span>
      <span class="brand__line">Construction Ltd</span>
    </div>
    <div class="band band--front">
      <div class="person">
        <p class="person__name">TOMASZ BRELWIK</p>
        <p class="person__title">Managing Director</p>
      </div>
      <div class="divider"></div>
      <ul class="contacts">
        <li>
          <svg viewBox="0 0 20 20" fill="none" stroke="#fff" stroke-width="1.8" stroke-linecap="round"><path d="M4 2.5l3 3-1.6 2.2c1 2.2 2.7 3.9 4.9 4.9l2.2-1.6 3 3-2 2.2C8.5 16 4 11.5 1.8 4.5z"/><path d="M12 2.5a5.5 5.5 0 0 1 5.5 5.5M12 5.5a2.5 2.5 0 0 1 2.5 2.5"/></svg>
          020 5194 6281
        </li>
        <li>
          <svg viewBox="0 0 20 20" fill="none" stroke="#fff" stroke-width="1.8"><rect x="5" y="1.5" width="10" height="17" rx="2"/><line x1="8.5" y1="15.5" x2="11.5" y2="15.5"/></svg>
          07845139072
        </li>
        <li>
          <svg viewBox="0 0 20 20" fill="none" stroke="#fff" stroke-width="1.6"><rect x="1.5" y="4" width="17" height="12"/><path d="M1.5 4l8.5 7 8.5-7M1.5 16l6-6M18.5 16l-6-6"/></svg>
          tomasz@varkelt.co.uk
        </li>
        <li>
          <svg viewBox="0 0 20 20" fill="none" stroke="#fff" stroke-width="1.5"><circle cx="10" cy="10" r="8"/><ellipse cx="10" cy="10" rx="3.5" ry="8"/><line x1="2" y1="10" x2="18" y2="10"/><path d="M3.5 5.5h13M3.5 14.5h13"/></svg>
          www.varkelt.co.uk
        </li>
      </ul>
    </div>
  </section>

  <section class="card card--back">
    <div class="brand brand--faint">
      <span class="brand__name">Varkelt</span>
      <span class="brand__line">Construction Ltd</span>
    </div>
    <div class="band band--back">
      <ul class="services services--one">
        <li>Kitchen Renovations</li>
        <li>Bathroom Renovations</li>
        <li>House Renovations</li>
        <li>Garage Conversions</li>
        <li>Extensions</li>
      </ul>
      <ul class="services services--two">
        <li>Loft Conversions</li>
        <li>Conservatories</li>
        <li>Carpentry</li>
        <li>Tiling</li>
        <li>Electrical</li>
      </ul>
      <ul class="services services--three">
        <li>Plumbing &amp; Heating</li>
        <li>Bricklaying</li>
        <li>Landscaping</li>
        <li>Decorating</li>
        <li>Plastering</li>
      </ul>
    </div>
  </section>

</div>
</body>
</html>
```